13 Varno - new website design project

Our company Varno Electrical is developing a new lead generation website focused on Electrical, LED Lighting and Solar Power. We need a high converting website.

Example of our current website is www.varnoelectrical-example.com.au You can take content from this website for this new design. Our colours are red, black and white. For our new website we would like to promote Varno, Spark Every Day. Please listen to the jingle.

The below link is the company jingle that we have developed.
http://www.tunecraftdemo.com.au/vrn-tc-v1/

The key for this brief is to generate leads for Electrical, LED Lighting (for commercial) and Solar Power & Storage.

Target Market(s)

Business owners in Melbourne Victoria

Number of Pages Required

4 page

Colors
ec1f27
ffffff

Requirements
Must have
• This page must be clean, be in line with company branding and a high converting lead website.

```html
<!DOCTYPE html>
<html lang="en">
<head>
<meta charset="utf-8">
<title>Varno Electrical</title>
<link href="https://fonts.googleapis.com/css2?family=Roboto:wght@400;500;700&family=Roboto+Condensed:wght@400;700&family=Open+Sans:wght@400;600&display=swap" rel="stylesheet">
<style>
:root{--red:#d31f2b;--red-dark:#b0151f;--ink:#222;--dark:#31333b;--dark-2:#2a2c33;--grey:#f1f1f1;--text:#555;--white:#fff;}
*{box-sizing:border-box;margin:0;padding:0}
html,body{width:1200px;height:3455px;overflow:hidden}
body{font-family:"Open Sans",Arial,sans-serif;color:var(--text);background:var(--white);position:relative}
.abs{position:absolute}
h2.section-title{position:absolute;left:0;width:1200px;text-align:center;font-family:"Roboto",sans-serif;font-weight:700;font-size:30px;color:var(--ink);letter-spacing:.5px}
h2.section-title span{color:var(--red)}
h2.section-title:after{content:"";display:block;width:60px;height:3px;background:var(--red);margin:18px auto 0}
/* header */
.site-header{position:absolute;top:0;left:0;width:1200px;height:132px;background:var(--white)}
.brand{position:absolute;left:80px;top:18px;display:flex;align-items:center;gap:12px}
.brand-dot{width:44px;height:44px;border-radius:50%;background:var(--red)}
.brand-name{font-family:"Roboto",sans-serif;font-weight:700;font-size:46px;color:var(--ink);line-height:1}
.brand-tag{position:absolute;left:136px;top:88px;font-family:"Roboto",sans-serif;font-size:16px;color:var(--red)}
.top-contacts{position:absolute;right:80px;top:20px;display:flex;align-items:center;gap:12px;font-size:14px;color:var(--ink)}
.icon-circle{width:30px;height:30px;border-radius:50%;border:2px solid var(--red);display:inline-flex;align-items:center;justify-content:center}
.social{width:30px;height:30px;border-radius:50%;background:var(--red);display:inline-block}
.main-nav{position:absolute;left:345px;top:80px;width:855px;height:52px;background:var(--red);display:flex;align-items:center;justify-content:space-around;padding:0 20px;clip-path:polygon(20px 0,100% 0,100% 100%,0 100%)}
.main-nav a{font-family:"Roboto",sans-serif;font-weight:700;font-size:15px;color:var(--white);text-decoration:none}
/* hero */
.hero{position:absolute;top:132px;left:0;width:1200px;height:588px;background:linear-gradient(100deg,#8b7355 0%,#c9b89a 30%,#e0dcd4 55%,#d7d4cc 100%)}
.hero-arc{position:absolute;right:0;top:0;width:560px;height:588px;background:radial-gradient(circle at 100% 50%,rgba(255,255,255,0) 0 230px,rgba(255,255,255,.55) 231px 260px,rgba(255,255,255,0) 261px)}
.hero-title{position:absolute;left:740px;top:230px;width:340px;text-align:right;font-family:"Roboto Condensed",sans-serif;font-weight:700;font-size:33px;line-height:38px;color:var(--ink)}
.dots{display:flex;gap:6px;justify-content:center}
.dots i{width:12px;height:12px;border-radius:50%;background:var(--ink);display:block}
.dots i.on{background:var(--red)}
/* services */
.service{position:absolute;top:660px;width:340px;height:282px;clip-path:polygon(0 0,100% 0,100% 78%,50% 100%,0 78%);padding-top:48px;text-align:center}
.service.red{background:var(--red)}
.service.dark{background:#4a4c53}
.service-inner{position:absolute;inset:10px;clip-path:polygon(0 0,100% 0,100% 78%,50% 100%,0 78%);border:2px solid rgba(255,255,255,.5)}
.service h3{position:absolute;left:0;width:100%;top:165px;font-family:"Roboto",sans-serif;font-weight:700;font-size:25px;color:var(--white)}
.service svg{position:relative}
/* about */
.about-text{position:absolute;left:95px;top:1078px;width:1010px;text-align:center;font-size:14.5px;line-height:24px}
.about-text p{margin-bottom:8px}
.btn{position:absolute;display:flex;align-items:center;gap:12px;background:var(--red);color:var(--white);font-family:"Roboto",sans-serif;font-weight:500;font-size:13px;padding:0 14px;height:40px}
.btn .arr{width:20px;height:20px;border-radius:50%;background:var(--dark);display:inline-flex;align-items:center;justify-content:center}
/* why */
.why{position:absolute;top:1365px;left:0;width:1200px;height:775px;background:var(--grey)}
.feature{position:absolute;width:260px;text-align:center}
.feature h4{font-family:"Roboto",sans-serif;font-weight:700;font-size:18px;color:var(--ink);margin-bottom:10px}
.feature p{font-size:12.5px;line-height:19px;color:var(--text)}
.mini-arrow{display:block;width:24px;height:24px;border-radius:50%;margin:12px auto 0;background:var(--red)}
.mini-arrow.dark{background:var(--dark)}
/* work */
.card{position:absolute;top:2290px;width:330px;height:405px;background:var(--white);border:1px solid #ddd}
.card-logo{height:78px;display:flex;align-items:center;justify-content:center;font-family:"Roboto",sans-serif;font-weight:700;font-size:34px}
.card-photo{height:135px;background:linear-gradient(180deg,#8a8f99,#c7c2b8);position:relative}
.zoom{position:absolute;right:8px;bottom:8px;width:38px;height:38px;border-radius:50%;background:rgba(255,255,255,.85)}
.card h5{font-family:"Roboto",sans-serif;font-weight:700;font-size:17px;color:var(--ink);margin:16px 20px 4px}
.card .role{font-size:14px;color:var(--ink);margin:0 20px 10px}
.card p.quote{font-size:13.5px;line-height:24px;margin:0 20px}
/* clients */
.clients{position:absolute;top:2810px;left:0;width:1200px;height:305px;background:var(--white);border-top:1px solid #eee}
.client{position:absolute;top:3015px;width:213px;height:100px;display:flex;align-items:center;justify-content:center;font-family:"Roboto",sans-serif;font-weight:700;font-size:28px;box-shadow:0 1px 4px rgba(0,0,0,.15)}
/* footer */
.site-footer{position:absolute;top:3115px;left:0;width:1200px;height:295px;background:var(--dark)}
.footer-col h6{font-family:"Roboto",sans-serif;font-weight:700;font-size:15px;color:var(--white);margin-bottom:22px}
.footer-col h6 span{color:var(--red)}
.footer-col{position:absolute;top:40px;color:#ddd;font-size:13px}
.footer-col li{list-style:none;margin-bottom:16px;font-size:12.5px}
.footer-col li.on{color:var(--red)}
.field{width:265px;height:34px;border:1px solid #888;margin-bottom:8px;padding:8px 12px;font-size:12px;color:#ccc}
.bottom-bar{position:absolute;top:3410px;left:0;width:1200px;height:45px;background:var(--red);color:var(--white);font-size:12px;display:flex;align-items:center;justify-content:space-between;padding:0 85px}
</style>
</head>
<body>

<header class="site-header">
  <div class="brand"><span class="brand-dot"></span><span class="brand-name">VARNO</span></div>
  <div class="brand-tag">Spark Every Day</div>
  <div class="top-contacts">
    <span class="icon-circle"><svg width="14" height="14" viewBox="0 0 24 24"><path d="M6 2l4 4-2 3c1 3 4 6 7 7l3-2 4 4-3 4C10 22 2 14 2 5z" fill="#222"/></svg></span><span>139204</span>
    <span class="icon-circle" style="margin-left:14px"><svg width="14" height="14" viewBox="0 0 24 24"><rect x="2" y="5" width="20" height="14" fill="none" stroke="#d31f2b" stroke-width="2"/><path d="M2 5l10 8 10-8" fill="none" stroke="#d31f2b" stroke-width="2"/></svg></span><span>service@varnoelectrical-example.com.au</span>
    <span class="social" style="margin-left:8px"></span><span class="social"></span><span class="social"></span>
  </div>
  <nav class="main-nav">
    <a>HOME</a><a>VARNO STORY</a><a>SERVICES</a><a>OUR WORK</a><a>CONTACT US</a>
  </nav>
</header>

<section class="hero" role="img" aria-label="Electrician in hard hat and hi-vis vest working on a switchboard">
  <div class="hero-arc"></div>
  <h1 class="hero-title">Australia's largest fully integrated Electrical &amp; Energy Solutions Provider</h1>
  <div class="dots abs" style="left:890px;top:414px"><i class="on"></i><i></i><i></i></div>
</section>

<div class="service red" style="left:80px"><div class="service-inner"></div>
  <svg width="90" height="90" viewBox="0 0 90 90"><g fill="none" stroke="#fff" stroke-width="7" stroke-linecap="round"><path d="M30 60 L55 35"/><path d="M48 22l20 20"/><path d="M15 75l15-15"/></g><path d="M45 25 L65 45 L50 60 L30 40z" fill="#fff"/><path d="M58 22l10-10M68 32l10-10" stroke="#fff" stroke-width="6" stroke-linecap="round"/></svg>
  <h3>ELECTRICAL</h3></div>
<div class="service dark" style="left:430px"><div class="service-inner"></div>
  <svg width="90" height="90" viewBox="0 0 90 90"><path d="M20 20 L70 20 L58 55 L32 55z" fill="#fff"/><rect x="34" y="58" width="22" height="8" fill="#fff"/><rect x="36" y="69" width="18" height="8" fill="#fff"/></svg>
  <h3>LED LIGHTING</h3></div>
<div class="service red" style="left:780px"><div class="service-inner"></div>
  <svg width="90" height="90" viewBox="0 0 90 90"><circle cx="38" cy="28" r="9" fill="#fff"/><g stroke="#fff" stroke-width="3"><path d="M38 10v6M38 40v6M20 28h6M50 28h6M25 15l4 4M47 37l4 4M25 41l4-4M47 19l4-4"/></g><path d="M30 55h48l-8 22H22z" fill="#fff"/><g stroke="#d31f2b" stroke-width="2"><path d="M46 55l-6 22M62 55l-6 22M27 66h47"/></g></svg>
  <h3>SOLAR POWER</h3></div>

<h2 class="section-title" style="top:1000px">ABOUT <span>VARNO</span></h2>
<div class="about-text">
  <p>Varno Electrical was formed to be an expert Electricity Contracting Company providing services to all Residential and Commercial Customers. With over 10 years of experience, Varno Electrical has developed a highly-experienced team of professionals that ensure all our customer expectations are met.</p>
  <p>Lorem ipsum dolor sit amet, consectetuer adipiscing elit, sed diam nonummy nibh euismod tincidunt ut laoreet dolore magna aliquam erat volutpat. Ut wisi enim ad minim veniam, quis nostrud exerci tation ullamcorper suscipit lobortis nisl ut aliquip ex ea commodo consequat. Duis autem vel eum iriure dolor in hendrerit in vulputate velit esse molestie consequat, vel illum dolore eu feugiat.</p>
</div>
<div class="btn" style="left:527px;top:1267px">READ MORE <span class="arr"><svg width="8" height="10" viewBox="0 0 8 10"><path d="M1 1l5 4-5 4" stroke="#fff" stroke-width="2" fill="none"/></svg></span></div>

<section class="why">
  <h2 class="section-title" style="top:56px">WHY <span>CHOOSE US?</span></h2>
  <div class="feature" style="left:80px;top:152px"><h4>Professional Service</h4><p>When you hire a Varno Electrical Electrician you will get a professional and well-presented Electrician that comes skilled and ready to do the job.</p><span class="mini-arrow"></span></div>
  <div class="feature" style="left:465px;top:152px"><h4>Value for Money</h4><p>We provide extremely competitive pricing, which means you get value for money on quality that is comparable to the best in the industry.</p><span class="mini-arrow"></span></div>
  <div class="feature" style="left:862px;top:152px"><h4>Fully insured</h4><p>Varno Electrical is fully insured and equipped to handle break downs and service call outs.</p><span class="mini-arrow"></span></div>

  <svg class="abs" style="left:0;top:280px" width="1200" height="240" viewBox="0 0 1200 240">
    <g fill="none" stroke-width="46">
      <path d="M80 120 A120 120 0 0 0 200 240" stroke="#d31f2b" transform="translate(0,-120)"/>
      <path d="M200 120 A100 100 0 0 0 400 120" stroke="#d31f2b"/>
      <path d="M400 120 A100 100 0 0 1 600 120" stroke="#31333b"/>
      <path d="M600 120 A100 100 0 0 0 800 120" stroke="#d31f2b"/>
      <path d="M800 120 A100 100 0 0 1 1000 120" stroke="#31333b"/>
      <path d="M1000 120 A100 100 0 0 0 1200 120" stroke="#d31f2b"/>
      <path d="M0 120 A100 100 0 0 0 200 120" stroke="#d31f2b"/>
    </g>
    <g fill="#fff" stroke="#e6e6e6" stroke-width="6">
      <circle cx="200" cy="120" r="76"/><circle cx="400" cy="120" r="76"/><circle cx="600" cy="120" r="76"/><circle cx="800" cy="120" r="76"/><circle cx="1000" cy="120" r="76"/>
    </g>
    <g fill="#31333b">
      <circle cx="190" cy="102" r="12"/><path d="M168 140c0-18 10-24 22-24s16 4 18 8v16z"/><circle cx="214" cy="134" r="10" fill="none" stroke="#31333b" stroke-width="5"/>
      <circle cx="400" cy="108" r="22"/><path d="M388 126l-8 30 12-6 8 10 4-34zM412 126l8 30-12-6-8 10-4-34z"/><path d="M400 94l4 9 10 1-7 7 2 10-9-5-9 5 2-10-7-7 10-1z" fill="#fff"/>
      <path d="M588 88h24l-6 10c16 8 24 22 24 36 0 14-14 18-30 18s-30-4-30-18c0-14 8-28 24-36z"/><text x="600" y="140" text-anchor="middle" fill="#fff" font-family="Roboto,sans-serif" font-weight="700" font-size="28">$</text>
      <circle cx="800" cy="122" r="26"/><path d="M790 110c6 4 12 0 14 8s-8 10-6 18M780 126h20M812 104c-4 8 4 10 2 20" stroke="#fff" stroke-width="3" fill="none"/>
      <path d="M1000 90l28 10v20c0 18-12 30-28 36-16-6-28-18-28-36v-20z"/><path d="M988 122l9 9 16-17" stroke="#fff" stroke-width="5" fill="none"/>
    </g>
  </svg>

  <div class="feature" style="left:270px;top:545px"><h4>5 year workmanship guarantee</h4><p>You can buy with confidence as all of our work has a 5 year workmanship guarantee. For your peace of mind, we unconditionally back our electrical work. We will come back to fix any problems at our own expense.</p><span class="mini-arrow dark"></span></div>
  <div class="feature" style="left:665px;top:545px"><h4>Environmentally friendly</h4><p>We a committed to reducing carbon emissions by installing Solar Power and upgrading sites to LED Lighting. In addition to reducing the carbon emissions we recycle Fluorescent Tubes, Highbay Globes, Metal and Cardboard.</p><span class="mini-arrow dark"></span></div>
</section>

<h2 class="section-title" style="top:2190px">OUR <span>WORK</span></h2>
<article class="card" style="left:80px">
  <div class="card-logo" style="background:#f5e600;color:#222">Outback Gear Depot</div>
  <div class="card-photo" role="img" aria-label="Retail store interior with lit aisles"><span class="zoom"></span></div>
  <h5>Liam Corrigan</h5><div class="role">Executive Outback Gear Depot</div>
  <p class="quote">The service, communication and after sales service of Varno Electrical has been awesome. We would strongly recommend them to any business contemplating upgrading.</p>
</article>
<article class="card" style="left:435px">
  <div class="card-logo" style="color:#d31f2b">Velvet Lane</div>
  <div class="card-photo" role="img" aria-label="Shop floor with bright ceiling lighting"><span class="zoom"></span></div>
  <h5>R. Delano</h5><div class="role">Balwyn North VIC</div>
  <p class="quote">They clean up after the job, explained everything I needed to know and answered all questions. very professional. Will use them again in the future!</p>
</article>
<article class="card" style="left:790px">
  <div class="card-logo" style="color:#1f7ab8">Steelmark Alloys</div>
  <div class="card-photo" role="img" aria-label="Large warehouse with high bay lighting"><span class="zoom"></span></div>
  <h5>T. Marsh</h5><div class="role">Cranbourne North VIC</div>
  <p class="quote">Excellent work and very professional. Marcus takes time to explain everything and demonstrate workings. Very clear precise and accurate.</p>
</article>
<div class="dots abs" style="left:576px;top:2734px"><i class="on"></i><i></i><i></i></div>

<section class="clients">
  <h2 class="section-title" style="top:50px">OUR SATISFIED <span>CLIENTS</span></h2>
</section>
<div class="client" style="left:130px;background:#fff;color:#d31f2b;font-size:26px">Velvet Lane</div>
<div class="client" style="left:372px;background:#f5e600;color:#222;font-size:20px">Outback Gear Depot</div>
<div class="client" style="left:614px;background:#e3262b;color:#fff">Heron Plumbing</div>
<div class="client" style="left:856px;background:#d71920;color:#fff">Golden Grill</div>

<footer class="site-footer">
  <div class="footer-col" style="left:80px"><h6>QUICK <span>LINKS</span></h6>
    <ul><li class="on">› Home</li><li>› Varno Story</li><li>› Services</li><li>› Our Work</li><li>› Contact Us</li></ul></div>
  <div class="footer-col" style="left:287px"><h6>CONTACT <span>DETAILS</span></h6>
    <div style="display:flex;gap:10px;margin-bottom:18px"><svg width="14" height="20" viewBox="0 0 14 20"><path d="M7 0a7 7 0 0 1 7 7c0 5-7 13-7 13S0 12 0 7a7 7 0 0 1 7-7z" fill="#d31f2b"/><circle cx="7" cy="7" r="2.5" fill="#31333b"/></svg><div style="line-height:19px"><b style="color:#fff">Varno</b><br>12/48 Hollis Rd, Glen Iris,<br>VIC 3146</div></div>
    <div style="display:flex;gap:10px;margin-bottom:22px"><svg width="14" height="14" viewBox="0 0 24 24"><path d="M6 2l4 4-2 3c1 3 4 6 7 7l3-2 4 4-3 4C10 22 2 14 2 5z" fill="#d31f2b"/></svg>139204</div>
    <div style="display:flex;gap:10px"><svg width="14" height="12" viewBox="0 0 24 18"><rect width="24" height="18" fill="#d31f2b"/><path d="M0 0l12 9 12-9" stroke="#31333b" stroke-width="2" fill="none"/></svg>service@varnoelectrical-example.com.au</div></div>
  <div class="footer-col" style="left:607px"><h6>QUICK <span>INQUIRY</span></h6>
    <div class="field">Name</div><div class="field">Email</div><div class="field">Message</div>
    <div class="btn" style="position:relative;height:30px;width:96px;font-size:11px;margin-top:6px">SUBMIT <span class="arr" style="background:none">›</span></div></div>
  <div class="abs" style="left:965px;top:80px;display:flex;align-items:center;gap:8px"><span class="brand-dot" style="width:30px;height:30px"></span><span class="brand-name" style="color:#fff;font-size:38px">VARNO</span></div>
  <div class="abs" style="left:1010px;top:128px;font-family:Roboto,sans-serif;font-size:12px;color:#ccc">Spark Every Day</div>
  <div class="abs" style="left:990px;top:162px;display:flex;gap:8px"><span class="social" style="width:26px;height:26px"></span><span class="social" style="width:26px;height:26px"></span><span class="social" style="width:26px;height:26px"></span></div>
</footer>
<div class="bottom-bar"><span>Copyright © 2017 Varno. All Right Reserved.</span><span>Terms and Conditions &nbsp;|&nbsp; Privacy</span></div>

</body>
</html>
```